Business Card Design

Business Card for professional consulting firm working with large financial institutions.

Target Market(s)

Executive buyers

Industry/Entity Type

Banking

Contact Information for Business Card

Mild creativity wanted. Not boring, but do elaborate artwork.

Font styles to use
Serif
Sans Serif

Colors

Designer to choose colors to be used in the design.

Requirements
Must have
• Standard business card features - company name, individual name, telephone, website, email, locations.
Nice to have
• Two colors
Should not have
• too many colors, fancy printing, cartoons.

```html
<!DOCTYPE html>
<html lang="en">
<head>
<meta charset="utf-8">
<title>t4advisors — Business Card</title>
<link href="https://fonts.googleapis.com/css2?family=Lato:wght@400;700&display=swap" rel="stylesheet">
<style>
  :root {
    --backdrop: #9a9a9a;
    --card-dark: #111111;
    --card-blue: #002d84;
    --brand-blue: #1d3c9e;
    --text-light: #f2f2f2;
    --rule: #8a8a8a;
    --shadow: rgba(0, 0, 0, 0.45);
  }
  html, body {
    margin: 0;
    padding: 0;
    width: 1200px;
    height: 900px;
    overflow: hidden;
    background: var(--backdrop);
    font-family: "Lato", Arial, sans-serif;
  }
  .stage {
    position: relative;
    width: 1200px;
    height: 900px;
  }
  .card {
    position: absolute;
    box-shadow: 2px 4px 6px var(--shadow);
  }
  .card-front {
    left: 120px;
    top: 275px;
    width: 477px;
    height: 295px;
    background: var(--card-dark);
    border-radius: 0 42px 0 42px;
    color: var(--text-light);
  }
  .card-back {
    left: 607px;
    top: 274px;
    width: 476px;
    height: 294px;
    background: var(--card-blue);
    border-radius: 46px 0 46px 0;
  }
  .brand-name {
    position: absolute;
    font-family: "Lato", Arial, sans-serif;
    font-weight: 400;
    white-space: nowrap;
    letter-spacing: 0.5px;
  }
  .card-front .brand-name {
    left: 240px;
    top: 94px;
    width: 200px;
    text-align: center;
    font-size: 24px;
    color: var(--brand-blue);
  }
  .card-back .brand-name {
    left: 0;
    top: 128px;
    width: 476px;
    text-align: center;
    font-size: 34px;
    color: #ffffff;
  }
  .holder-name {
    position: absolute;
    left: 28px;
    top: 168px;
    margin: 0;
    font-size: 17px;
    font-weight: 400;
    color: var(--brand-blue);
    letter-spacing: 0.2px;
  }
  .holder-title {
    position: absolute;
    left: 29px;
    top: 187px;
    margin: 0;
    font-size: 13px;
    color: var(--text-light);
  }
  .title-rule {
    position: absolute;
    left: 157px;
    top: 193px;
    width: 293px;
    height: 1px;
    background: var(--rule);
  }
  .address {
    position: absolute;
    left: 28px;
    top: 233px;
    margin: 0;
    font-style: normal;
    font-size: 13.5px;
    line-height: 18px;
  }
  .contact-list {
    position: absolute;
    right: 30px;
    top: 216px;
    margin: 0;
    padding: 0;
    list-style: none;
    font-size: 13.5px;
    line-height: 18px;
    text-align: right;
  }
  .contact-list li {
    display: flex;
    justify-content: flex-end;
    align-items: center;
    gap: 5px;
  }
  .contact-icon {
    width: 11px;
    height: 11px;
    flex: none;
  }
</style>
</head>
<body>
<main class="stage">
  <section class="card card-front" aria-label="Business card front">
    <span class="brand-name">t4advisors</span>
    <h1 class="holder-name">JONATHAN SMITH</h1>
    <p class="holder-title">Managing Director</p>
    <div class="title-rule"></div>
    <address class="address">12345, Address Goes Here<br>Country Name, 123456.</address>
    <ul class="contact-list">
      <li>044-123 456 789
        <svg class="contact-icon" viewBox="0 0 12 12" aria-hidden="true"><path fill="#1d3c9e" d="M1 3.5C1 2 2 1 3.5 1h5C10 1 11 2 11 3.5V4H8.5V3h-5v1H1zM2 5h8l1 5.5H1zM6 6.3a1.8 1.8 0 1 0 0 3.6 1.8 1.8 0 1 0 0-3.6z"/></svg>
      </li>
      <li>info@webname.com
        <svg class="contact-icon" viewBox="0 0 12 12" aria-hidden="true"><rect x="0.5" y="2.5" width="11" height="7.5" fill="#1d3c9e"/><path d="M0.8 2.8 6 7l5.2-4.2" fill="none" stroke="#111" stroke-width="1"/></svg>
      </li>
      <li>www.websitename.com
        <svg class="contact-icon" viewBox="0 0 12 12" aria-hidden="true"><circle cx="6" cy="6" r="5.3" fill="#1d3c9e"/><path d="M1 6h10M6 0.8c-2.2 2.6-2.2 7.8 0 10.4M6 0.8c2.2 2.6 2.2 7.8 0 10.4" fill="none" stroke="#111" stroke-width="0.7"/></svg>
      </li>
    </ul>
  </section>

  <section class="card card-back" aria-label="Business card back">
    <span class="brand-name">t4advisors</span>
  </section>
</main>
</body>
</html>
```